Design the 21st Harborlight Open Cinema Showcase Poster. Think modern, chic, cool, film, movies - driving people to the film festival - the film festivla is in San Francisco and the SF East Bay. Our logo is attached. Dates will be determined soon . please use - November 2 - 11, 2018 (for placement) Keep in mind abstract, chic, modern - eye catching. website is www.hlocs-fest.org

Target Market(s)

25 - 45 year old - upper middle class

Industry/Entity Type

Film Production

Colors

Designer to choose colors to be used in the design.

Requirements
Must have
• logo (attached) www.hlocs-fest.org - chic modern design
Nice to have
• best coolest poster ever!
Should not have
• CLIP ART!!!

```html
<!DOCTYPE html>
<html lang="en">
<head>
<meta charset="utf-8">
<title>21st Harborlight Open Cinema Showcase – Poster</title>
<link rel="stylesheet" href="https://fonts.googleapis.com/css2?family=Montserrat:wght@300;400;500;600&display=swap">
<style>
  :root {
    --page-bg: #ffffff;
    --frame-line: #3a3a3a;
    --poster-red: #e10000;
    --poster-red-deep: #9a0000;
    --ink-white: #ffffff;
    --logo-green: #7cc242;
  }
  html, body {
    margin: 0;
    width: 1200px;
    height: 806px;
    overflow: hidden;
    background: var(--page-bg);
  }
  .canvas {
    position: relative;
    width: 1200px;
    height: 806px;
  }
  .poster {
    position: absolute;
    left: 330px;
    top: 21px;
    width: 540px;
    height: 764px;
    box-sizing: border-box;
    border: 2px solid var(--frame-line);
    background: var(--page-bg);
    padding: 11px;
  }
  .poster-art {
    display: block;
    width: 514px;
    height: 738px;
    font-family: "Montserrat", sans-serif;
  }
  .poster-art text { fill: var(--ink-white); }
  .rule { fill: var(--ink-white); }
  .brand-name { font-weight: 500; font-size: 34px; letter-spacing: 2px; }
  .brand-tag { font-weight: 500; font-size: 15px; }
  .edition { font-weight: 300; font-size: 146px; letter-spacing: -4px; }
  .title-small { font-weight: 400; font-size: 40px; }
  .title-large { font-weight: 500; font-size: 80px; }
  .dates { font-weight: 500; font-size: 32px; }
  .web { font-weight: 600; font-size: 15px; letter-spacing: 0.5px; }
</style>
</head>
<body>
<main class="canvas">
  <article class="poster">
    <svg class="poster-art" viewBox="0 0 514 738" xmlns="http://www.w3.org/2000/svg">
      <defs>
        <linearGradient id="bridgeShade" x1="0" y1="0" x2="0" y2="1">
          <stop offset="0" stop-color="#5a0000"/>
          <stop offset="0.55" stop-color="#b00000"/>
          <stop offset="1" stop-color="#e10000"/>
        </linearGradient>
      </defs>

      <rect class="poster-bg" width="514" height="738" fill="var(--poster-red)"/>

      <rect class="hero-photo" x="290" y="0" width="224" height="540" fill="url(#bridgeShade)" opacity="0.55"
            role="img" aria-label="Suspension bridge tower rising through fog, tinted red"/>

      <!-- vertical rule -->
      <rect class="rule" x="138" y="0" width="8" height="36"/>
      <rect class="rule" x="138" y="142" width="8" height="182"/>
      <rect class="rule" x="138" y="343" width="8" height="185"/>

      <!-- brand -->
      <circle class="brand-dot" cx="142" cy="62" r="15" fill="var(--logo-green)"/>
      <text class="brand-name" x="66" y="111">HLOCS</text>
      <text class="brand-tag" x="66" y="134">PRESENTS</text>

      <!-- edition -->
      <text class="edition" x="60" y="444">2</text>
      <text class="edition" x="152" y="444">st</text>

      <!-- title -->
      <text class="title-small" x="153" y="487" textLength="268" lengthAdjust="spacingAndGlyphs">HARBORLIGHT</text>
      <text class="title-small" x="153" y="521" textLength="290" lengthAdjust="spacingAndGlyphs">OPEN CINEMA</text>
      <text class="title-large" x="62" y="590">OPEN</text>
      <text class="title-large" x="62" y="652" textLength="400" lengthAdjust="spacingAndGlyphs">SHOWCASE</text>

      <text class="dates" x="62" y="685" textLength="400" lengthAdjust="spacingAndGlyphs">NOVEMBER 2 – 11, 2018</text>
      <text class="web" x="257" y="724" text-anchor="middle">WWW.HLOCS-FEST.ORG</text>
    </svg>
  </article>
</main>
</body>
</html>
```